VELQUINT

1. My company will allow people to buy either stock made or custom scented aromatherapy candles, lotions,soaps,body sprays, and wax melts. As there isn't a company that allows for custom oil scent mixes but me. We are just starting with the candles and the other items will be coming later.

2. My target audience is anyone who would want to buy my product. It isn't really limited due to the nature of the product I will be providing.

3. velquint.com is the domain name (purchased from plorvex.com).

4. So what I really need is the shopping cart function. A fully coded shopping cart that will calculate shipping and sales tax if need be. I need the cart function to be just like every other major retailers shopping cart function. So they can click on an item they want and have it go into a shopping cart for the customer to then be able to go and pay for their goods. I also need help creating single pages for each product. So that each thing we make has a separate page with a description and an add to cart button.

5. I would like the color scheme to follow the logo I made. I would also like the logo top center of first page. I would like the quote " elevate your choices in aromatherapy products"

^. I basically need a checkout just like every other good website. A clear shipping area for them to populate, sales tax calculator, ya know everything a normal checkout has like tressly or dunvexa.com. I also have a vonk account already as well.

```html
<!DOCTYPE html>
<html lang="en">
<head>
<meta charset="utf-8">
<title>VELQUINT — Aromatherapy Candles</title>
<link href="https://fonts.googleapis.com/css2?family=Playfair+Display:wght@700&family=Roboto:wght@400;500;700&family=Poppins:wght@400;500&display=swap" rel="stylesheet">
<style>
:root{
  --ink:#111111;
  --black:#000000;
  --white:#ffffff;
  --blue:#36a9f5;
  --blue-deep:#3b82f0;
  --purple:#6a3bc8;
  --grad:linear-gradient(90deg,#36a9f5 0%,#5a63dc 60%,#6a3bc8 100%);
  --price:#3b7fe0;
  --muted:#555555;
  --card-bg:linear-gradient(135deg,#dbeafb,#ece4fb);
}
*{box-sizing:border-box;margin:0;padding:0}
html,body{width:1200px;height:3428px;overflow:hidden}
body{position:relative;background:var(--white);font-family:"Roboto",sans-serif;color:var(--ink)}
.abs{position:absolute}
.serif{font-family:"Playfair Display",serif;font-weight:700}
.btn{position:absolute;display:flex;align-items:center;justify-content:center;gap:8px;background:var(--grad);color:var(--white);font-weight:700;font-size:14px;text-transform:uppercase;letter-spacing:.2px}
.btn svg{width:13px;height:13px}
.ornament{position:absolute;left:50%;transform:translateX(-50%);width:40px;height:40px;border-radius:50%;background:var(--grad)}
.ornament.light{background:linear-gradient(135deg,#ffffff,#cfcfe8)}
.section-title{position:absolute;left:0;width:1200px;text-align:center;font-size:44px}

/* hero */
.hero{position:absolute;left:0;top:0;width:1200px;height:601px;background:radial-gradient(ellipse at 70% 40%,#1c1826 0%,#0b0b0d 60%,#050506 100%);border-top:3px solid #6a3bc8}
.nav a{position:absolute;top:60px;color:var(--white);font-size:14px;font-weight:700;text-decoration:none;text-transform:uppercase}
.nav a.active{color:var(--blue)}
.brand{position:absolute;left:500px;top:40px;width:200px;display:flex;flex-direction:column;align-items:center;gap:10px}
.brand-dot{width:44px;height:44px;border-radius:50%;background:var(--grad)}
.brand-name{font-family:"Playfair Display",serif;font-weight:700;font-size:22px;color:var(--white);letter-spacing:3px}
.icon-btn{position:absolute;top:50px;width:38px;height:38px;border-radius:50%;background:var(--grad);display:flex;align-items:center;justify-content:center}
.icon-btn svg{width:16px;height:16px}
.hero h1{position:absolute;left:111px;top:198px;font-size:44px;line-height:49px;color:var(--white)}
.hero h1 span{color:var(--blue-deep)}
.hero p{position:absolute;left:111px;top:366px;width:400px;color:var(--white);font-weight:700;font-size:13.5px;line-height:26px;text-transform:uppercase}
.hero-media{position:absolute;left:512px;top:126px;width:688px;height:370px;border-radius:30px 0 0 30px;background:radial-gradient(ellipse at 45% 55%,#8a6bd0 0%,#5b3f9a 45%,rgba(20,16,30,0) 78%)}

/* marquee */
.marquee{position:absolute;left:0;top:601px;width:1200px;height:62px;background:var(--grad);overflow:hidden;white-space:nowrap}
.marquee span{position:absolute;top:22px;color:var(--white);font-weight:700;font-size:14px}

/* products */
.card{position:absolute;top:895px;width:218px;height:257px;background:var(--card-bg);border:3px solid #f3f3f3;box-shadow:0 2px 8px rgba(0,0,0,.08)}
.card.active{background:var(--grad);border-color:transparent}
.card .cart{position:absolute;right:14px;top:14px;width:42px;height:42px;border-radius:50%;background:var(--grad);display:flex;align-items:center;justify-content:center}
.card.active .cart{background:var(--black)}
.card .cart svg{width:18px;height:18px}
.card .shot{position:absolute;left:34px;top:70px;width:150px;height:150px;border-radius:50%}
.prod-name{position:absolute;top:1174px;width:218px;text-align:center;font-weight:500;font-size:18px}
.prod-price{position:absolute;top:1206px;width:218px;text-align:center;font-weight:500;font-size:18px;color:var(--price)}
.arrow{position:absolute;width:50px;height:50px;border-radius:50%;display:flex;align-items:center;justify-content:center;background:var(--black)}
.arrow.next{background:var(--grad);box-shadow:0 0 0 3px #1a1a2a}
.arrow svg{width:16px;height:16px}

/* create */
.create{position:absolute;left:0;top:1384px;width:1200px;height:765px;background:radial-gradient(ellipse at 50% 60%,#1a1a1d 0%,#070708 70%)}
.create .sub{position:absolute;left:0;top:222px;width:1200px;text-align:center;color:var(--white);font-weight:700;font-size:17px}
.bottles{position:absolute;left:206px;top:279px;width:780px;height:307px;border-radius:8px;background:linear-gradient(180deg,#2c2c30 0%,#1a1a1c 55%,#5a4030 75%,#1b1b1d 100%)}
.flower-l{position:absolute;left:0;top:460px;width:130px;height:230px;border-radius:0 50% 50% 0;background:radial-gradient(circle,#9a82cf,#4d3a7d 70%,rgba(0,0,0,0))}
.flower-r{position:absolute;left:1030px;top:150px;width:170px;height:260px;border-radius:50% 0 0 50%;background:radial-gradient(circle,#a58fd8,#5a4590 70%,rgba(0,0,0,0))}

/* testimonials */
.tcard{position:absolute;top:2388px;width:314px;height:233px;background:var(--white);padding:26px 22px}
.tcard.focus{box-shadow:0 6px 18px rgba(0,0,0,.14)}
.avatar{position:absolute;left:22px;top:28px;width:66px;height:66px;border-radius:50%;background:linear-gradient(135deg,#cfd3da,#6b7380)}
.tname{position:absolute;left:108px;top:40px;font-family:"Poppins",sans-serif;font-weight:500;font-size:16px}
.trole{position:absolute;left:108px;top:64px;font-family:"Poppins",sans-serif;font-size:14px;color:var(--muted)}
.rating{position:absolute;left:222px;top:48px;display:flex;align-items:center;gap:5px}
.rating i{width:18px;height:18px;border-radius:50%;background:#4285f4;display:block}
.rating b{color:#f5b400;font-size:12px;letter-spacing:1px}
.tbody{position:absolute;left:22px;top:122px;width:280px;font-family:"Poppins",sans-serif;font-size:12.5px;line-height:21.5px;color:#333}

/* newsletter */
.footer-bg{position:absolute;left:0;top:2900px;width:1200px;height:528px;background:var(--black)}
.news{position:absolute;left:109px;top:2714px;width:975px;height:310px;background:var(--grad);border:2px solid #e0e0e0}
.news .kick{position:absolute;left:40px;top:52px;color:var(--white);font-weight:700;font-size:22px}
.news h3{position:absolute;left:40px;top:90px;color:var(--white);font-size:37px}
.news p{position:absolute;left:40px;top:154px;width:480px;color:var(--white);font-weight:700;font-size:17px;line-height:26px}
.news .cta{position:absolute;left:38px;top:213px;width:282px;height:51px;background:var(--black);color:var(--white);display:flex;align-items:center;justify-content:center;gap:8px;font-weight:700;font-size:14px}
.news .cta svg{width:13px;height:13px}
.news-media{position:absolute;left:575px;top:26px;width:320px;height:253px;border-radius:40% 40% 10px 10px;background:radial-gradient(ellipse at 50% 60%,#8a8f75 0%,#4f5b4a 45%,rgba(90,99,220,0) 75%)}

/* footer */
.f-brand{position:absolute;left:117px;top:3130px;width:123px;display:flex;flex-direction:column;align-items:center;gap:10px}
.f-brand .brand-name{font-size:20px}
.fcol{position:absolute;top:3120px;color:var(--white)}
.fcol h4{font-weight:500;font-size:18px;margin-bottom:14px}
.fcol a{display:block;color:var(--white);text-decoration:none;font-size:14.5px;line-height:24px}
.fcol .small{font-size:10.5px;line-height:19px;width:200px}
.email{margin-top:18px;width:191px;height:40px;background:#1e1e1e;display:flex;align-items:center;justify-content:space-between;padding:0 4px 0 10px;font-size:9px}
.email b{width:32px;height:26px;background:var(--grad);display:flex;align-items:center;justify-content:center}
.email b svg{width:10px;height:10px}
.socials{display:flex;gap:10px;margin-top:20px}
.socials i{display:block;width:28px;height:28px;border-radius:50%;background:var(--grad);border:2px solid #fff}
.pays{display:flex;gap:5px;margin-top:18px}
.pays i{display:block;width:22px;height:13px;border-radius:2px;background:#f2f2f2}
.rule{position:absolute;left:170px;top:3336px;width:868px;height:1px;background:#3a3a3a}
.copy{position:absolute;left:0;top:3370px;width:1200px;text-align:center;color:var(--white);font-size:9.5px;font-weight:500}
</style>
</head>
<body>

<!-- Header / hero -->
<section class="hero">
  <nav class="nav">
    <a class="active" style="left:111px" href="#">Home</a>
    <a style="left:177px" href="#">Shop</a>
    <a style="left:245px" href="#">Custom Scents</a>
    <a style="left:392px" href="#">FAQ</a>
    <a style="left:747px" href="#">About Us</a>
    <a style="left:842px" href="#">Contact Us</a>
  </nav>
  <div class="brand"><span class="brand-dot"></span><span class="brand-name">VELQUINT</span></div>
  <span class="icon-btn" style="left:965px"><svg viewBox="0 0 16 16" fill="none" stroke="#fff" stroke-width="2.2"><circle cx="7" cy="7" r="4.5"/><path d="M10.5 10.5L14 14"/></svg></span>
  <span class="icon-btn" style="left:1006px"><svg viewBox="0 0 16 16" fill="#fff"><path d="M1 2h2.5l2 8h7.5l1.8-5.5H5"/><circle cx="6.5" cy="13" r="1.3"/><circle cx="12" cy="13" r="1.3"/></svg></span>
  <span class="icon-btn" style="left:1047px"><svg viewBox="0 0 16 16" fill="#fff"><circle cx="8" cy="5" r="3.2"/><path d="M2 15c0-4 2.7-6 6-6s6 2 6 6z"/></svg></span>

  <h1 class="serif">Elevate Your Choices<br>in <span>Aromatherapy<br>Products</span></h1>
  <p>Handcrafted, premium aromatherapy candles and self-care products – including your own custom scent blends.</p>
  <a class="btn" style="left:111px;top:464px;width:231px;height:44px" href="#">Shop Our Products <svg viewBox="0 0 14 14"><circle cx="7" cy="7" r="7" fill="#fff"/><path d="M5.5 4l3 3-3 3" stroke="#4a6be0" stroke-width="2" fill="none"/></svg></a>
  <div class="hero-media" role="img" aria-label="Lavender flowers, lit candles, a bowl of white stones, a folded towel and dropper bottles"></div>
</section>

<div class="marquee">
  <span style="left:40px">FREE SHIPPING</span><span style="left:186px">TRY NOW</span>
  <span style="left:313px">FREE SHIPPING</span><span style="left:459px">TRY NOW</span>
  <span style="left:586px">FREE SHIPPING</span><span style="left:732px">TRY NOW</span>
  <span style="left:859px">FREE SHIPPING</span><span style="left:1005px">TRY NOW</span>
  <span style="left:1132px">FREE SHIPPING</span>
</div>

<!-- Best sellers -->
<span class="ornament" style="top:735px" role="img" aria-label="Brand star ornament"></span>
<h2 class="section-title serif" style="top:784px">Best Sellers</h2>

<span class="arrow" style="left:36px;top:1001px"><svg viewBox="0 0 16 16" fill="none" stroke="#fff" stroke-width="2"><path d="M8 4L4 8l4 4M13 4L9 8l4 4"/></svg></span>
<span class="arrow next" style="left:1107px;top:1001px"><svg viewBox="0 0 16 16" fill="none" stroke="#fff" stroke-width="2"><path d="M3 4l4 4-4 4M8 4l4 4-4 4"/></svg></span>

<div class="card" style="left:113px"><span class="cart"><svg viewBox="0 0 16 16" fill="#fff"><path d="M1 2h2.5l2 8h7.5l1.8-5.5H5"/><circle cx="6.5" cy="13" r="1.3"/><circle cx="12" cy="13" r="1.3"/></svg></span><div class="shot" role="img" aria-label="Amber glass candle" style="background:radial-gradient(circle,#f5a623,#e07a10 60%,rgba(0,0,0,0) 72%)"></div></div>
<div class="prod-name" style="left:113px">LAVENDER BLISS</div><div class="prod-price" style="left:110px">$ 30.00</div>

<div class="card" style="left:363px"><span class="cart"><svg viewBox="0 0 16 16" fill="#fff"><path d="M1 2h2.5l2 8h7.5l1.8-5.5H5"/><circle cx="6.5" cy="13" r="1.3"/><circle cx="12" cy="13" r="1.3"/></svg></span><div class="shot" role="img" aria-label="Amber dropper bottle with white label" style="background:radial-gradient(ellipse 35% 50%,#7a4a22,#b08060 60%,rgba(0,0,0,0) 75%)"></div></div>
<div class="prod-name" style="left:363px">LAVENDER BLISS</div><div class="prod-price" style="left:360px">$ 30.00</div>

<div class="card active" style="left:613px"><span class="cart"><svg viewBox="0 0 16 16" fill="#fff"><path d="M1 2h2.5l2 8h7.5l1.8-5.5H5"/><circle cx="6.5" cy="13" r="1.3"/><circle cx="12" cy="13" r="1.3"/></svg></span><div class="shot" role="img" aria-label="Amber dropper bottle with gold label" style="background:radial-gradient(ellipse 35% 50%,#8a5a2a,#c29a70 60%,rgba(0,0,0,0) 75%)"></div></div>
<div class="prod-name" style="left:613px">LAVENDER BLISS</div><div class="prod-price" style="left:610px">$ 30.00</div>

<div class="card" style="left:865px"><span class="cart"><svg viewBox="0 0 16 16" fill="#fff"><path d="M1 2h2.5l2 8h7.5l1.8-5.5H5"/><circle cx="6.5" cy="13" r="1.3"/><circle cx="12" cy="13" r="1.3"/></svg></span><div class="shot" role="img" aria-label="Olive green glass candle" style="background:radial-gradient(circle,#8a8d4a,#5a5c30 60%,rgba(0,0,0,0) 72%)"></div></div>
<div class="prod-name" style="left:865px">LAVENDER BLISS</div><div class="prod-price" style="left:862px">$ 30.00</div>

<a class="btn" style="left:492px;top:1254px;width:214px;height:46px" href="#">Upcoming Products <svg viewBox="0 0 14 14"><circle cx="7" cy="7" r="7" fill="#fff"/><path d="M5.5 4l3 3-3 3" stroke="#4a6be0" stroke-width="2" fill="none"/></svg></a>

<!-- Create your scent -->
<section class="create">
  <span class="ornament light" style="top:88px" role="img" aria-label="Brand star ornament"></span>
  <h2 class="section-title serif" style="top:142px;color:var(--white)">Create Your Perfect Scent</h2>
  <div class="sub">Your scent, your way! Mix and match essential oils to create a blend that’s uniquely yours.</div>
  <div class="flower-r" role="img" aria-label="Purple flowers"></div>
  <div class="flower-l" role="img" aria-label="Purple flowers"></div>
  <div class="bottles" role="img" aria-label="Black dropper bottles and jars arranged on a wooden stand"></div>
  <a class="btn" style="left:502px;top:606px;width:214px;height:44px" href="#">Create Your Blend <svg viewBox="0 0 14 14"><circle cx="7" cy="7" r="7" fill="#fff"/><path d="M5.5 4l3 3-3 3" stroke="#4a6be0" stroke-width="2" fill="none"/></svg></a>
</section>

<!-- Testimonials -->
<span class="ornament" style="top:2232px" role="img" aria-label="Brand star ornament"></span>
<h2 class="section-title serif" style="top:2290px">Customer Testimonials</h2>

<span class="arrow" style="left:36px;top:2480px"><svg viewBox="0 0 16 16" fill="none" stroke="#fff" stroke-width="2"><path d="M8 4L4 8l4 4M13 4L9 8l4 4"/></svg></span>
<span class="arrow next" style="left:1107px;top:2480px;box-shadow:none"><svg viewBox="0 0 16 16" fill="none" stroke="#fff" stroke-width="2"><path d="M3 4l4 4-4 4M8 4l4 4-4 4"/></svg></span>

<div class="tcard" style="left:113px">
  <div class="avatar" role="img" aria-label="Customer portrait"></div>
  <div class="tname">Dorian Vell</div><div class="trole">Manager</div>
  <div class="rating"><i></i><b>★★★★★</b></div>
  <p class="tbody">Lorem ipsum dolor sit amet, consectetur adipiscing elit, sed do eiusmod tempor incididunt ut labore et dolore magna aliqua. Ut enim ad minim veniamea .</p>
</div>
<div class="tcard focus" style="left:443px">
  <div class="avatar" role="img" aria-label="Customer portrait"></div>
  <div class="tname">Marla Quen</div><div class="trole">Manager</div>
  <div class="rating"><i></i><b>★★★★★</b></div>
  <p class="tbody">Lorem ipsum dolor sit amet, consectetur adipiscing elit, sed do eiusmod tempor incididunt ut labore et dolore magna aliqua. Ut enim ad minim veniamea .</p>
</div>
<div class="tcard" style="left:772px">
  <div class="avatar" role="img" aria-label="Customer portrait"></div>
  <div class="tname">Tobin Rask</div><div class="trole">Manager</div>
  <div class="rating"><i></i><b>★★★★★</b></div>
  <p class="tbody">Lorem ipsum dolor sit amet, consectetur adipiscing elit, sed do eiusmod tempor incididunt ut labore et dolore magna aliqua. Ut enim ad minim veniamea .</p>
</div>

<!-- Footer -->
<div class="footer-bg"></div>

<section class="news">
  <div class="kick">GET 10% OFF YOUR FIRST ORDER!</div>
  <h3 class="serif">Join our community</h3>
  <p>Be the first to know about exclusive scents, special offers, and self-care tips."</p>
  <a class="cta" href="#">SIGNUP OUR NEWSLETTER <svg viewBox="0 0 14 14"><circle cx="7" cy="7" r="7" fill="#fff"/><path d="M5.5 4l3 3-3 3" stroke="#000" stroke-width="2" fill="none"/></svg></a>
  <div class="news-media" role="img" aria-label="Plant, stone candle holder and amber bottles on a dark stone"></div>
</section>

<div class="f-brand"><span class="brand-dot"></span><span class="brand-name">VELQUINT</span></div>

<div class="fcol" style="left:339px">
  <h4>Information</h4>
  <a href="#">Our Products</a><a href="#">Benefits</a><a href="#">How it Works</a><a href="#">Testimonials</a><a href="#">Faq</a><a href="#">Contact</a>
</div>
<div class="fcol" style="left:510px">
  <h4>Service</h4>
  <a href="#">Payment options</a><a href="#">Shipping and Returns</a><a href="#">Armptherapy Products</a><a href="#">Get offer</a>
</div>
<div class="fcol" style="left:716px">
  <h4>Get in Touch</h4>
  <p class="small">Sign up for our newsletter and receive exclusive monthly discounts and updates on our newest laundry fragrances!</p>
  <div class="email">ENTER EMAIL <b><svg viewBox="0 0 10 10" fill="none" stroke="#fff" stroke-width="1.6"><path d="M3 2l3 3-3 3"/></svg></b></div>
</div>
<div class="fcol" style="left:965px">
  <h4>Contact us</h4>
  <a href="#">hello@velquint.com</a>
  <div class="socials"><i></i><i></i><i></i></div>
  <div class="pays"><i></i><i></i><i></i><i></i><i></i></div>
</div>

<div class="rule"></div>
<div class="copy">COPYRIGHT@2025 - ALL RIGHTS RESERVED</div>

</body>
</html>
```